Companybrochure for Consulting & Financing Firm

I need to have a Company Brochure asap for our company. We have a website that describes what we do, but we need also a brochure, that can be sent by PDF of eventually be printed as well.

The brochure should be short but nice and appealing to the customers.

We provide professional management consulting and help our customers to get finance for very diferent projects. Our business has a lot to do with personal relations, but also we are very professional in the way we work and how develop the solutions for our clients. Our clients are mainly government-owned firm, but also private trading companies and wealthy private investors.

Our customers are mainly in Latin America, but the company is headquater is in Switzerland. We are opening offices in Panama and Caracas, this should be easaly be adabtable later.

Please have a look at our website www.vorelpartners.ch. In the brochure, we would segment our services in 1.) Project Developments 2.) Management Conulting 3.) Investment Management and 4.) Finance Solutions.

Also do have a look at www.vorelpartners.ch
(Click E for the English version)
Updates

I managed to put the Mock-Up to the Website.
It is actually not really a mock-up, it is a version I have designed myself.
Well as I am not a designer, I hope you can make it much better.
The content however is what I would put in any other design as well.

Target Market(s)

Top Management, Investors, Entrepreneurs, Government Officials

Industry/Entity Type

Management Consulting

Requirements
Must have
• Design should reflect this image elements:

We are entrepreneurs.
We are comitted to get things done.
We work closely with the client side by side.
We are a professional partner.
We are not afraid of delivering unconventional solutions.
We look at the problem from various angles.
We analyse, develop solutions and implent results.
Should not have
• Typical US-American style elements. We do not want to give the impression of being a US company.

We do not want to appear to be neo-liberal. We are a politically neutral professional consulting firm.

```html
<!DOCTYPE html>
<html lang="en">
<head>
<meta charset="utf-8">
<title>Vorel Partners AG – Company Brochure</title>
<link href="https://fonts.googleapis.com/css2?family=Montserrat:wght@700;800&family=PT+Sans:wght@400;700&family=Roboto+Condensed:wght@400&display=swap" rel="stylesheet">
<style>
  :root {
    --navy: #2b2a78;
    --indigo: #2c2a8c;
    --sky: #2aa5dc;
    --line: #29a3e0;
    --panel: #dfe6f0;
    --ink: #333333;
    --grey: #4a4a4a;
    --paper: #ffffff;
    --backdrop: #e6e8eb;
  }
  * { margin: 0; padding: 0; box-sizing: border-box; }
  html, body { width: 1200px; height: 830px; overflow: hidden; background: var(--backdrop); }
  .page {
    position: absolute; top: 26px; width: 549px; height: 776px;
    background: linear-gradient(180deg, #f1f3f6 0%, var(--paper) 30%, var(--paper) 100%);
    box-shadow: 0 2px 8px rgba(0,0,0,.18); overflow: hidden;
  }
  .page--cover { left: 30px; }
  .page--back { left: 617px; }
  .page__art { position: absolute; inset: 0; }
  .motto {
    position: absolute; left: 0; right: 0; text-align: center;
    font-family: "Montserrat", sans-serif; font-weight: 800; letter-spacing: .5px;
  }
  .motto .dot {
    display: inline-block; width: 11px; height: 11px; border-radius: 50%;
    border: 3px solid var(--sky); margin: 0 10px; vertical-align: middle; position: relative; top: -2px;
  }
  .cover__motto { top: 408px; font-size: 22px; color: #fff; }
  .company-name {
    position: absolute; font-family: "PT Sans", sans-serif; font-weight: 700;
  }
  .cover__name { left: 0; right: 0; top: 522px; text-align: center; font-size: 36px; color: var(--ink); }
  .cover__intro {
    position: absolute; right: 45px; top: 650px; text-align: right; color: #fff;
    font-family: "PT Sans", sans-serif; font-size: 15px; line-height: 20px;
  }
  .services {
    position: absolute; top: 707px; left: 0; width: 549px; list-style: none;
    font-family: "Roboto Condensed", sans-serif; font-size: 16px; color: #fff;
  }
  .services li { position: absolute; white-space: nowrap; text-align: right; }
  .services li::after { content: " \25C2"; font-size: 14px; }
  .services .c1 { right: 271px; }
  .services .c2 { right: 48px; }
  .services .r2 { top: 28px; }
  .values {
    position: absolute; left: 30px; top: 66px; width: 490px; height: 352px;
    background: var(--panel); border: 2px solid var(--line); border-radius: 32px;
    list-style: none; padding: 35px 0 0 38px;
    font-family: "Roboto Condensed", sans-serif; font-size: 17px; color: var(--indigo);
  }
  .values li { height: 42.4px; display: flex; align-items: flex-start; gap: 8px; }
  .values svg { flex: none; margin-top: 3px; }
  .back__motto { top: 488px; font-size: 24px; color: var(--navy); }
  .back__motto .dot { border-color: var(--line); width: 13px; height: 13px; }
  .back__note {
    position: absolute; left: 0; right: 0; top: 527px; text-align: center;
    font-family: "Roboto Condensed", sans-serif; font-size: 16px; color: var(--grey);
  }
  .back__name { right: 29px; top: 662px; font-size: 25px; color: #e4e8f0; }
  .contact {
    position: absolute; top: 709px; font-family: "PT Sans", sans-serif; font-weight: 700;
    font-size: 11.5px; line-height: 16.5px; color: #fff; font-style: normal;
  }
  .contact--address { left: 27px; }
  .contact--phone { left: 214px; top: 725.5px; }
  .contact--web { left: 395px; top: 725.5px; }
</style>
</head>
<body>

<section class="page page--cover">
  <svg class="page__art" width="549" height="776" viewBox="0 0 549 776">
    <defs>
      <linearGradient id="bandBlue" x1="0" y1="0" x2="1" y2="0">
        <stop offset="0" stop-color="#2b2a78"/>
        <stop offset="1" stop-color="#2aa5dc"/>
      </linearGradient>
      <linearGradient id="photoTone" x1="0" y1="0" x2="1" y2="0.3">
        <stop offset="0" stop-color="#1a1f2e"/>
        <stop offset=".45" stop-color="#1d3f72"/>
        <stop offset="1" stop-color="#2c8fd6"/>
      </linearGradient>
    </defs>
    <path d="M0,270 L0,528 C180,470 380,450 549,452 L549,238 Z" fill="url(#bandBlue)"/>
    <path d="M0,522 C180,462 380,442 549,444" fill="none" stroke="var(--line)" stroke-width="2"/>
    <ellipse cx="274" cy="216" rx="280" ry="178" transform="rotate(-8 274 216)" fill="#fff"/>
    <ellipse cx="274" cy="216" rx="272" ry="170" transform="rotate(-8 274 216)" fill="none" stroke="#1f6fb8" stroke-width="1.5"/>
    <ellipse cx="274" cy="210" rx="264" ry="160" transform="rotate(-8 274 210)" fill="url(#photoTone)" role="img" aria-label="Photo of a consultant writing business keywords on a glass board over a world map"/>
    <path d="M0,674 C180,625 380,602 549,600 L549,776 L0,776 Z" fill="url(#bandBlue)"/>
    <path d="M0,668 C180,618 380,596 549,594" fill="none" stroke="var(--line)" stroke-width="2"/>
  </svg>

  <p class="motto cover__motto">ANALYZE<span class="dot"></span>DEVELOP<span class="dot"></span>DELIVER</p>
  <h1 class="company-name cover__name">Vorel Partners AG</h1>
  <p class="cover__intro">We are a professional consulting, financing and<br>investment firm operating in the fields of:</p>
  <ul class="services">
    <li class="c1">Project Development</li>
    <li class="c2">Investment Management</li>
    <li class="c1 r2">Management Consulting</li>
    <li class="c2 r2">Finance Solutions</li>
  </ul>
</section>

<section class="page page--back">
  <svg class="page__art" width="549" height="776" viewBox="0 0 549 776">
    <defs>
      <linearGradient id="bandBlueBack" x1="0" y1="0" x2="1" y2="0">
        <stop offset="0" stop-color="#2b2a78"/>
        <stop offset="1" stop-color="#2aa5dc"/>
      </linearGradient>
    </defs>
    <path d="M0,670 C180,622 380,602 549,602 L549,776 L0,776 Z" fill="url(#bandBlueBack)"/>
    <path d="M0,664 C180,615 380,595 549,595" fill="none" stroke="var(--line)" stroke-width="2"/>
  </svg>

  <ul class="values">
    <li><svg width="15" height="14" viewBox="0 0 15 14"><rect x="1" y="3" width="10" height="10" fill="none" stroke="#f08a24" stroke-width="1.5"/><path d="M3.5 7.5 L6.5 10.5 L14 1.5" fill="none" stroke="#f08a24" stroke-width="2"/></svg>We are entrepreneurs.</li>
    <li><svg width="15" height="14" viewBox="0 0 15 14"><rect x="1" y="3" width="10" height="10" fill="none" stroke="#f08a24" stroke-width="1.5"/><path d="M3.5 7.5 L6.5 10.5 L14 1.5" fill="none" stroke="#f08a24" stroke-width="2"/></svg>We are comitted to get things done.</li>
    <li><svg width="15" height="14" viewBox="0 0 15 14"><rect x="1" y="3" width="10" height="10" fill="none" stroke="#f08a24" stroke-width="1.5"/><path d="M3.5 7.5 L6.5 10.5 L14 1.5" fill="none" stroke="#f08a24" stroke-width="2"/></svg>We work closely with the client side by side.</li>
    <li><svg width="15" height="14" viewBox="0 0 15 14"><rect x="1" y="3" width="10" height="10" fill="none" stroke="#f08a24" stroke-width="1.5"/><path d="M3.5 7.5 L6.5 10.5 L14 1.5" fill="none" stroke="#f08a24" stroke-width="2"/></svg>We are a professional partner.</li>
    <li><svg width="15" height="14" viewBox="0 0 15 14"><rect x="1" y="3" width="10" height="10" fill="none" stroke="#f08a24" stroke-width="1.5"/><path d="M3.5 7.5 L6.5 10.5 L14 1.5" fill="none" stroke="#f08a24" stroke-width="2"/></svg>We are not afraid of delivering unconventional solutions.</li>
    <li><svg width="15" height="14" viewBox="0 0 15 14"><rect x="1" y="3" width="10" height="10" fill="none" stroke="#f08a24" stroke-width="1.5"/><path d="M3.5 7.5 L6.5 10.5 L14 1.5" fill="none" stroke="#f08a24" stroke-width="2"/></svg>We look at the problem from various angles</li>
    <li><svg width="15" height="14" viewBox="0 0 15 14"><rect x="1" y="3" width="10" height="10" fill="none" stroke="#f08a24" stroke-width="1.5"/><path d="M3.5 7.5 L6.5 10.5 L14 1.5" fill="none" stroke="#f08a24" stroke-width="2"/></svg>.We analyse, develop solutions and implent results.</li>
  </ul>

  <p class="motto back__motto">ANALYZE<span class="dot"></span>DEVELOP<span class="dot"></span>DELIVER</p>
  <p class="back__note">Vorel Partners AG is registered as a Swiss stock corporation since 1995.</p>

  <p class="company-name back__name">Vorel Partners AG</p>
  <address class="contact contact--address">Vorel Partners AG<br>Lindenweg 14<br>CH-8004 Zürich</address>
  <address class="contact contact--phone">Tel. &nbsp;+41 44 210 35 80<br>Fax. +41 44 210 35 81</address>
  <address class="contact contact--web">www.vorelpartners.ch<br>info@vorelpartners.ch</address>
</section>

</body>
</html>
```